Email Signature Design

Please design an email signature, the below is an example of our current design;
___

HARCOURT ESTATE PARTNERS PTY LTD
DOMINIC FARRADAY
Licensed Strata and Community Manager

148 Calloway Street,
KELDON NSW 2048

P: 02.9374.6082 F: 9463.7820
Website: www.harcourtestate.com.au

This e-mail message and accompanying data may contain information that is confidential and private. If you are not the intended recipient, the use, dissemination, distribution or copying of this message or data is prohibited.

If you have received this e-mail in error please notify us immediately and delete all material pertaining to this e-mail. office@harcourtestate.com.au

___

We would like to incorporate our logo and company colours, you can view the colours and feel of image at www.harcourtestate.com.au

Industry/Entity Type

It Company

Requirements
Must have
• use of logo and company colours (image)

```html
<!DOCTYPE html>
<html lang="en">
<head>
<meta charset="utf-8">
<title>Harcourt Estate Partners – Email Signature</title>
<link rel="stylesheet" href="https://fonts.googleapis.com/css2?family=Source+Sans+3:wght@400;700&display=swap">
<style>
  :root {
    --page: #efefef;
    --card: #ffffff;
    --olive: #7b7a3a;
    --slate: #6d6e70;
    --ink-light: #ffffff;
    --edge: #4a4a4a;
  }
  * { box-sizing: border-box; margin: 0; padding: 0; }
  html, body {
    width: 1200px; height: 440px; overflow: hidden;
    background: var(--page);
    font-family: "Source Sans 3", "Myriad Pro", Arial, sans-serif;
  }
  .signature {
    position: absolute; left: 28px; top: 34px;
    width: 1132px; height: 377px;
    background: var(--card);
    border: 1px solid var(--edge);
    display: flex;
  }
  .brand-side {
    position: relative; width: 607px; height: 100%;
  }
  .brand-name {
    position: absolute; left: 86px; top: 240px;
    font-size: 30px; font-weight: 700; letter-spacing: 0.4px;
    color: var(--slate); white-space: nowrap; line-height: 1.1;
  }
  .divider {
    width: 4px; height: 100%; background: var(--olive);
  }
  .contact-side {
    flex: 1; margin-left: 3px; height: 100%;
    background: var(--slate); color: var(--ink-light);
    padding: 52px 0 0 34px;
  }
  .person-name { font-size: 22px; font-weight: 700; line-height: 26px; }
  .person-role { font-size: 21px; font-weight: 400; line-height: 28px; }
  .company { margin-top: 22px; font-size: 21px; line-height: 28px; }
  .contact-list { list-style: none; margin-top: 28px; }
  .contact-list li {
    display: flex; align-items: center; gap: 10px;
    font-size: 21px; line-height: 29.5px;
  }
  .contact-list svg { width: 18px; height: 18px; flex: none; }
</style>
</head>
<body>
  <main class="signature">
    <section class="brand-side">
      <div class="brand-name">HARCOURT ESTATE PARTNERS</div>
    </section>
    <div class="divider"></div>
    <section class="contact-side">
      <div class="person-name">DOMINIC FARRADAY</div>
      <div class="person-role">Licensed Strata and Community Manager</div>
      <div class="company">HARCOURT ESTATE PARTNERS PTY LTD<br>148 Calloway Street, KELDON NSW 2048</div>
      <ul class="contact-list">
        <li>
          <svg viewBox="0 0 20 20" aria-hidden="true"><circle cx="10" cy="10" r="8.5" fill="none" stroke="#fff" stroke-width="1.5"/><path d="M7 5.5c-1.5 2.5-.5 6.5 3 9l1.5-1.5-1.6-1.8-.9.6c-1-1-1.5-2.2-1.5-3.5l1-.4-.3-2.4z" fill="#fff"/></svg>
          02.9374.6082
        </li>
        <li>
          <svg viewBox="0 0 20 20" aria-hidden="true"><rect x="5" y="2" width="10" height="6" fill="#fff"/><rect x="2" y="8" width="16" height="8" rx="1" fill="#fff"/><rect x="5" y="11" width="10" height="2" fill="#6d6e70"/></svg>
          9463.7820
        </li>
        <li>
          <svg viewBox="0 0 20 20" aria-hidden="true"><rect x="2" y="5" width="16" height="11" fill="#fff"/><path d="M2 5l8 6 8-6" fill="none" stroke="#6d6e70" stroke-width="1.4"/></svg>
          office@harcourtestate.com.au
        </li>
        <li>
          <svg viewBox="0 0 20 20" aria-hidden="true"><g fill="none" stroke="#fff" stroke-width="1.3"><circle cx="10" cy="10" r="8"/><ellipse cx="10" cy="10" rx="3.5" ry="8"/><path d="M2 10h16M3.5 6h13M3.5 14h13"/></g></svg>
          www.harcourtestate.com.au
        </li>
      </ul>
    </section>
  </main>
</body>
</html>
```